1 Page for Computer Repair Website

Looking for a 1 page website with a design that compliments the business card and pamphlet that have already been made (attached files). It should look business professional and easy to read. Email and phone number should be somewhere near the top of the website, visible when the page loads. I don't want any forms for people to mess with. No "Contact Us" form or entering in email for newsletter. Customers will just be looking at this site to confirm we are professionals and have our business in order.

Target Market(s)

Home and small business

Industry/Entity Type

Computer Repair

Coding

Coded - Design and coding required

Number of Pages Required

1 page

Font styles to use
Other font styles liked:
• Helvetica variations used in pamphlet and card

Colors
0455a3
cfdeed
85abd2
3276b5
85cae6
ffffff

Requirements
Must have
• Compliment the pamphlet and business card in color choices and font use. Pleasing to the eye and easy to read through categories and text.
Should not have
• Forms. No "enter name and email here" or anything of the sort.

```html
<!DOCTYPE html>
<html lang="en">
<head>
<meta charset="utf-8">
<title>Bytewell Computer Services</title>
<link href="https://fonts.googleapis.com/css2?family=Open+Sans:wght@400;600;700;800&display=swap" rel="stylesheet">
<style>
:root{
  --brand:#0455a3;
  --brand-mid:#3276b5;
  --brand-soft:#85abd2;
  --sky:#85cae6;
  --ice:#cfdeed;
  --white:#ffffff;
  --ink:#2a2a2a;
  --muted:#8a8a8a;
  --footer:#1d1d1f;
  --footer-bar:#141415;
  --footer-text:#a9a9a9;
}
*{margin:0;padding:0;box-sizing:border-box}
html,body{width:696px;height:1200px;overflow:hidden;background:var(--white)}
body{font-family:"Open Sans",Helvetica,Arial,sans-serif;color:var(--ink);position:relative}
.site-header{height:97px;position:relative}
.brand{position:absolute;left:28px;top:16px;font-size:25px;font-weight:700;color:var(--brand);letter-spacing:-.5px;line-height:1}
.brand-tag{position:absolute;left:30px;top:44px;font-size:7.5px;color:var(--brand-mid);letter-spacing:.5px}
.top-contact{position:absolute;right:40px;top:18px;display:flex;gap:18px;font-size:8px;color:#555}
.top-contact span{display:flex;align-items:center;gap:5px}
.top-contact svg{width:11px;height:11px}
.main-nav{position:absolute;left:70px;right:70px;top:58px;height:30px;background:var(--brand);display:flex}
.main-nav a{font-size:7.5px;font-weight:600;color:var(--white);text-decoration:none;display:flex;align-items:center;padding:0 24px;text-transform:uppercase}
.main-nav a.active{background:var(--brand-mid)}
.hero{position:absolute;top:97px;left:0;width:696px;height:333px;background:linear-gradient(135deg,#b48a5c 0%,#d6b68a 45%,#8f6a45 100%)}
.services{position:absolute;top:430px;left:0;width:696px;text-align:center}
.services h2{margin-top:28px;font-size:22px;font-weight:800;color:#222}
.section-sub{font-size:7px;color:var(--muted);margin-top:4px}
.dots{display:flex;justify-content:center;gap:4px;margin-top:6px}
.dots i{width:4px;height:4px;border-radius:50%;background:var(--brand-soft)}
.service-grid{position:absolute;top:108px;left:56px;width:590px;display:grid;grid-template-columns:repeat(3,1fr);row-gap:30px;column-gap:20px;text-align:left}
.service{display:flex;gap:10px}
.service-icon{width:22px;height:22px;background:var(--brand);flex:none;display:flex;align-items:center;justify-content:center}
.service-icon svg{width:12px;height:12px}
.service h3{font-size:8px;font-weight:700;color:#222;margin-bottom:3px}
.service p{font-size:6.5px;line-height:1.55;color:var(--muted)}
.about{position:absolute;top:770px;left:0;width:696px;height:200px}
.about-media{position:absolute;left:92px;top:12px;width:280px;height:180px;background:linear-gradient(180deg,var(--ice),#e9eef3 60%,#c9d3de);border-radius:4px}
.about-copy{position:absolute;left:385px;top:20px;width:220px}
.about-copy h2{font-size:20px;font-weight:800;color:#222;margin-bottom:10px}
.about-copy p{font-size:6.5px;line-height:1.6;color:var(--muted);margin-bottom:8px}
.more-btn{display:inline-block;border:1px solid #bbb;font-size:6.5px;padding:4px 12px;color:#555}
.site-footer{position:absolute;top:1002px;left:0;width:696px;height:170px;background:var(--footer);color:var(--footer-text)}
.footer-cols{position:absolute;left:58px;top:22px;display:grid;grid-template-columns:150px 100px 150px 160px;gap:14px}
.site-footer h4{font-size:9px;font-weight:700;color:var(--white);margin-bottom:10px;letter-spacing:.3px}
.site-footer p,.site-footer li{font-size:6.5px;line-height:1.65}
.site-footer ul{list-style:none}
.site-footer li{display:flex;align-items:center;gap:5px;margin-bottom:3px}
.site-footer li svg{width:8px;height:8px;flex:none}
.social{display:flex;gap:5px}
.social i{width:14px;height:14px;border-radius:50%;background:#3a3a3d}
.footer-bar{position:absolute;top:1172px;left:0;width:696px;height:28px;background:var(--footer-bar);font-size:6.5px;color:#888;display:flex;align-items:center;justify-content:center}
</style>
</head>
<body>
<header class="site-header">
  <div class="brand">Bytewell</div>
  <div class="brand-tag">Computer Services</div>
  <div class="top-contact">
    <span><svg viewBox="0 0 12 12"><rect width="12" height="12" rx="2" fill="#0455a3"/><path d="M3.5 3h1.5l.7 1.6-.9.7a4.5 4.5 0 0 0 1.9 1.9l.7-.9 1.6.7V8.5A.8.8 0 0 1 8.3 9 5.3 5.3 0 0 1 3 3.7.8.8 0 0 1 3.5 3z" fill="#fff"/></svg>Call: (555) 014-2276</span>
    <span><svg viewBox="0 0 12 12"><rect width="12" height="12" rx="2" fill="#0455a3"/><path d="M2.5 4h7v4.5h-7zM2.5 4l3.5 2.6L9.5 4" stroke="#fff" stroke-width=".8" fill="none"/></svg>Email: hello@bytewell.example</span>
  </div>
  <nav class="main-nav">
    <a class="active">Home</a><a>About Us</a><a>Services</a><a>Why Choose Us</a><a>Testimonials</a><a>Contact Us</a>
  </nav>
</header>

<div class="hero" role="img" aria-label="Top-down photo of a wooden desk with a laptop, tablet, phone, mouse, calculator and coffee cup"></div>

<section class="services">
  <h2>OUR SERVICES</h2>
  <p class="section-sub">Friendly, fast repairs for homes and small offices. We fix it right and explain every step along the way.</p>
  <div class="dots"><i></i><i></i><i></i></div>
  <div class="service-grid">
    <div class="service"><div class="service-icon"><svg viewBox="0 0 12 12"><path d="M6 1l4 1.5v3C10 8 8 10 6 11 4 10 2 8 2 5.5v-3z" fill="#fff"/></svg></div><div><h3>Malware/Virus Removal</h3><p>We clean infected machines, remove unwanted programs and restore safe, smooth daily use.</p></div></div>
    <div class="service"><div class="service-icon"><svg viewBox="0 0 12 12"><rect x="1.5" y="2" width="9" height="6" fill="#fff"/><rect x="4" y="9" width="4" height="1.2" fill="#fff"/></svg></div><div><h3>PC/Mac/Laptop Hardware Repair</h3><p>Screens, keyboards, drives and power faults diagnosed and repaired with quality parts.</p></div></div>
    <div class="service"><div class="service-icon"><svg viewBox="0 0 12 12"><path d="M6 1.5l4 4.5H7.5v4.5h-3V6H2z" fill="#fff"/></svg></div><div><h3>Upgrades</h3><p>Add memory, faster storage or new components to give older computers fresh speed.</p></div></div>
    <div class="service"><div class="service-icon"><svg viewBox="0 0 12 12"><path d="M2 4h6V2.5L11 5 8 7.5V6H2zM10 8H4V6.5L1 9l3 2.5V10h6z" fill="#fff"/></svg></div><div><h3>Data Migration</h3><p>Move files, settings and programs safely from your old computer to the new one.</p></div></div>
    <div class="service"><div class="service-icon"><svg viewBox="0 0 12 12"><ellipse cx="6" cy="3" rx="4" ry="1.5" fill="#fff"/><path d="M2 3v6c0 .8 1.8 1.5 4 1.5s4-.7 4-1.5V3" fill="#fff"/></svg></div><div><h3>Data Rescue</h3><p>Recover photos, documents and records from failed or damaged drives when possible.</p></div></div>
    <div class="service"><div class="service-icon"><svg viewBox="0 0 12 12"><circle cx="6" cy="6" r="4.5" fill="none" stroke="#fff" stroke-width="1.3"/><path d="M6 6l2.5-2" stroke="#fff" stroke-width="1.3"/></svg></div><div><h3>Tune Ups</h3><p>Cleanup, updates and startup checks that keep your system running at its best.</p></div></div>
    <div class="service"><div class="service-icon"><svg viewBox="0 0 12 12"><path d="M2.5 6.2l2.3 2.3L9.5 3.5" stroke="#fff" stroke-width="1.6" fill="none"/></svg></div><div><h3>AntiVirus Installation</h3><p>Reliable protection installed, configured and updated so threats stay out.</p></div></div>
    <div class="service"><div class="service-icon"><svg viewBox="0 0 12 12"><rect x="1.5" y="2" width="9" height="6" fill="none" stroke="#fff" stroke-width="1.2"/><path d="M4 10h4" stroke="#fff" stroke-width="1.2"/></svg></div><div><h3>Remote Support</h3><p>Quick help over a secure connection without leaving your home or office.</p></div></div>
    <div class="service"><div class="service-icon"><svg viewBox="0 0 12 12"><path d="M10 6a4 4 0 1 1-1.2-2.8M9 1.5v2.2H6.8" stroke="#fff" stroke-width="1.2" fill="none"/></svg></div><div><h3>PC Format</h3><p>Full wipe and clean reinstall of your operating system and core software.</p></div></div>
  </div>
</section>

<section class="about">
  <div class="about-media" role="img" aria-label="Technician working on an open desktop computer, shown on a monitor, laptop, tablet and phone"></div>
  <div class="about-copy">
    <h2>ABOUT BYTEWELL</h2>
    <p>We are a local repair team serving homes and small businesses. Every job starts with a clear diagnosis and an honest quote before any work begins, so there are no surprises.</p>
    <p>With years of hands-on experience we repair, upgrade and protect all kinds of computers. Our goal is simple: dependable machines and customers who feel confident in the work we do.</p>
    <span class="more-btn">More Info</span>
  </div>
</section>

<footer class="site-footer">
  <div class="footer-cols">
    <div>
      <h4>BRAND SUPPORT</h4>
      <p>Bytewell keeps local homes and offices running with careful repairs, clear pricing and friendly service. Bring your computer in or call us for help today.</p>
    </div>
    <div>
      <h4>NAVIGATION</h4>
      <ul><li>› Home</li><li>› About Us</li><li>› Services</li><li>› Support</li><li>› Contact</li></ul>
    </div>
    <div>
      <h4>GET IN TOUCH</h4>
      <ul>
        <li><svg viewBox="0 0 8 8"><path d="M4 .5a2.5 2.5 0 0 1 2.5 2.5C6.5 5 4 7.5 4 7.5S1.5 5 1.5 3A2.5 2.5 0 0 1 4 .5z" fill="#85cae6"/></svg>48 Harbor Lane, Riverton</li>
        <li><svg viewBox="0 0 8 8"><rect x=".5" y="1.5" width="7" height="5" fill="#85cae6"/></svg>hello@bytewell.example</li>
        <li><svg viewBox="0 0 8 8"><circle cx="4" cy="4" r="3.5" fill="#85cae6"/></svg>Phone: (555) 014-2276</li>
      </ul>
    </div>
    <div>
      <h4>CONNECT ONLINE</h4>
      <div class="social"><i></i><i></i><i></i><i></i><i></i><i></i></div>
    </div>
  </div>
</footer>
<div class="footer-bar">© Copyright 2015 Bytewell | All Rights Reserved</div>
</body>
</html>
```